www.marvenholt.com

Updating website so looks futristic but yet business like and easy to navigate, essentially a good landing page with a cool picture summing up what we do, and links to the following pages, all other pages on site to be updated, Exclusive Distributor of Brisk Forge Unique Fitness Equipment Products in UK & Ireland, www.crestvolley.co.uk Exclusive Partners & Distributors Of Crest Volley - Obstacle Races - Obstacle Hire - Obstacle Training - Adventure Events, www.goplumwick.co.uk Adventures That Inspire. We also Health Club / Facillity Consultancy

```html
<!DOCTYPE html>
<html lang="en">
<head>
<meta charset="utf-8">
<title>Marvenholt Leisure — Services</title>
<link rel="stylesheet" href="https://fonts.googleapis.com/css2?family=Barlow+Condensed:wght@400;600&display=swap">
<style>
  :root {
    --bg: #121212;
    --bg-deep: #080808;
    --text: #f2f2f2;
    --accent: #e0761f;
    --rule: #d8d8d8;
    --photo-light: #b9b9b9;
    --photo-mid: #5a5a5a;
  }
  * { margin: 0; padding: 0; box-sizing: border-box; }
  html, body {
    width: 1093px;
    height: 1200px;
    overflow: hidden;
  }
  body {
    background: radial-gradient(ellipse at 50% 40%, #1c1c1c 0%, var(--bg) 55%, var(--bg-deep) 100%);
    color: var(--text);
    font-family: "Barlow Condensed", "Arial Narrow", sans-serif;
    position: relative;
  }
  .service { position: absolute; left: 0; width: 1093px; }
  .service-photo {
    position: absolute;
    background: radial-gradient(ellipse at 55% 45%, var(--photo-light) 0%, var(--photo-mid) 45%, rgba(18,18,18,0) 75%);
  }
  .service-copy { position: absolute; width: 410px; }
  .service-title {
    font-weight: 600;
    font-size: 35px;
    letter-spacing: 0.3px;
    line-height: 1;
    color: #fff;
  }
  .title-rule {
    display: block;
    height: 2px;
    background: var(--rule);
    margin-top: 9px;
    margin-bottom: 16px;
  }
  .service-text {
    font-size: 13.4px;
    line-height: 18.4px;
    margin-bottom: 18.4px;
    color: var(--text);
  }
  .brand { color: var(--accent); }
  .service-link {
    display: inline-block;
    margin-top: 12px;
    margin-left: 3px;
    font-size: 17px;
    color: #fff;
    text-decoration: none;
    border-bottom: 1px solid #fff;
    line-height: 1.15;
  }
  .divider {
    position: absolute;
    left: 210px;
    width: 656px;
    height: 2px;
    background: linear-gradient(90deg, rgba(224,118,31,0), var(--accent) 20%, var(--accent) 80%, rgba(224,118,31,0));
  }
</style>
</head>
<body>

<section class="service service--fitness" style="top:0;height:485px;">
  <div class="service-photo" role="img" aria-label="Black and white photo of a smiling woman and a man training together on gym rowing equipment" style="left:446px;top:0;width:647px;height:474px;"></div>
  <div class="service-copy" style="left:61px;top:15px;">
    <h2 class="service-title">COMMERCIAL FITNESS</h2>
    <span class="title-rule" style="width:122px;margin-left:3px;"></span>
    <p class="service-text"><span class="brand">Marvenholt Leisure</span> long term success depends on the talents commitment and shared values of our people, Marvenholt Leisure is made of a unique hand picked team that will ensure the best possible service is delivered, as a company were passionate about delivering the best for our clients so we employ and partner with the best people who share that drive, passion and are led through the Marvenholt values in everything they do.</p>
    <p class="service-text">Our philosophy is based on open genuine collaborations working with organisations, who like us have a can do attitude proactive approach and who want to win, with over 25 years experience in the Health, Wellness and Fitness Industry and many hundreds of happy clients we want to help build your business the right way!</p>
    <a class="service-link" href="#">VISIT BRISK FORGE &gt;</a>
  </div>
</section>

<div class="divider" style="top:484px;"></div>

<section class="service service--events" style="top:486px;height:496px;">
  <div class="service-photo" role="img" aria-label="Black and white photo of a mud-covered obstacle racer crawling through mud" style="left:27px;top:6px;width:611px;height:474px;background:radial-gradient(ellipse at 45% 45%, var(--photo-light) 0%, var(--photo-mid) 45%, rgba(18,18,18,0) 75%);"></div>
  <div class="service-copy" style="left:638px;top:44px;">
    <h2 class="service-title" style="margin-left:6px;">OCR / EVENTS</h2>
    <span class="title-rule" style="width:141px;margin-left:2px;"></span>
    <p class="service-text"><span class="brand">Marvenholt Leisure</span> long term success depends on the talents commitment and shared values of our people, Marvenholt Leisure is made of a unique hand picked team that will ensure the best possible service is delivered, as a company were passionate about delivering the best for our clients so we employ and partner with the best people who share that drive, passion and are led through the Marvenholt values in everything they do.</p>
    <p class="service-text">Our philosophy is based on open genuine collaborations working with organisations, who like us have a can do attitude proactive approach and who want to win, with over 25 years experience in the Health, Wellness and Fitness Industry and many hundreds of happy clients we want to help build your business the right way!</p>
  </div>
</section>

<div class="divider" style="top:981px;"></div>

<section class="service service--consultancy" style="top:983px;height:217px;">
  <div class="service-photo" role="img" aria-label="Black and white photo of two men in discussion at a health club" style="left:455px;top:10px;width:638px;height:420px;background:radial-gradient(ellipse at 60% 50%, var(--photo-light) 0%, var(--photo-mid) 45%, rgba(18,18,18,0) 75%);"></div>
  <div class="service-copy" style="left:58px;top:36px;width:405px;">
    <h2 class="service-title">CONSULTANCY</h2>
    <span class="title-rule" style="width:108px;margin-left:2px;"></span>
    <p class="service-text"><span class="brand">Marvenholt Leisure</span> long term success depends on the talents commitment and shared values of our people, Marvenholt Leisure is made of a unique hand picked team that will ensure the best possible service is delivered, as a company were passionate about delivering the best for our clients so we employ and partner with the best people who share that drive, passion and are led through the Marvenholt values in everything they do.</p>
  </div>
</section>

</body>
</html>
```